Website creation for audiovisual activities

I want a website for my director of photography activity. It's primarily composed of screenshots in gallery format, followed by detailed pages for each production.

Here's my current website:
www.lionelbaquet.com
I'd like a more modern and streamlined design, and for the site to be responsive on phones and computers. I also want to be able to easily add photos and text to it later.

Target Market(s)

productions society, directors and producers.

Industry/Entity Type

Audiovisual / TV

Coding

Coded - Design and coding required

Number of Pages Required

5+ page

Font styles to use
Sans Serif

Colors
0054AA
0677BA
7BADD7
CADEEF
E8F1F8
0094D4
00A9DD
6FCCEA
C7EBF8
E9F6FB
00AB8E
00BBA5
67D7C9
C6EFE9
E9F9F6
6B429C
8869AF
B7A5CE
E3DAEB
F3F0F8

Requirements
Must have
• a modern look with a photo gallery on the homepage
Nice to have
• a light background with large, dynamic images
Should not have
• a dark background and an overly classic look

```html
<!DOCTYPE html>
<html lang="fr">
<head>
<meta charset="utf-8">
<title>Marc Deleval – Directeur Photo</title>
<link href="https://fonts.googleapis.com/css2?family=Inter:wght@300;400;500;600&family=Rubik:wght@700;800&display=swap" rel="stylesheet">
<style>
:root{
  --board:#232323;
  --navy:#15368f;
  --blue:#1a44a8;
  --blue-hero:#17399a;
  --beige:#c8b497;
  --beige-text:#f3ece2;
  --ink:#1b1b1b;
  --muted:#6d6d6d;
  --white:#ffffff;
  --story-bg:#e8eef7;
}
*{box-sizing:border-box;margin:0;padding:0}
html,body{width:1200px;height:1185px;overflow:hidden;background:var(--board)}
body{font-family:"Inter",Arial,sans-serif;color:var(--ink)}
.board{position:absolute;left:0;top:0;width:1932px;height:1908px;background:var(--board);transform:scale(.62112);transform-origin:0 0}
.screen{position:absolute;width:515px;background:var(--white);overflow:hidden}
.screen--home{left:108px;top:98px;height:1415px}
.screen--magazine{left:709px;top:98px;height:816px}
.screen--detail{left:1309px;top:98px;height:753px}
.screen--partner{left:709px;top:995px;height:815px}
.abs{position:absolute}

/* header */
.site-header{position:absolute;left:0;top:0;width:100%;height:46px;background:var(--white)}
.logo{position:absolute;left:47px;top:11px}
.logo__name{font-size:14px;font-weight:400;color:var(--navy);letter-spacing:.2px;line-height:14px;display:block}
.logo__tag{font-size:9px;color:var(--beige);letter-spacing:1px;line-height:11px;display:block;padding-left:17px}
.nav{position:absolute;top:18px;font-size:6.5px;color:#333;white-space:nowrap}
.nav--active{color:var(--beige);text-decoration:underline}
.btn{position:absolute;display:flex;align-items:center;justify-content:center;background:var(--navy);color:var(--white);border-radius:9px;font-size:6px;font-weight:500;white-space:nowrap}
.btn--header{left:417px;top:15px;width:50px;height:16px}
.pill{position:absolute;display:flex;align-items:center;justify-content:center;height:16px;border-radius:8px;font-size:6px;color:var(--navy);background:var(--white);box-shadow:0 1px 4px rgba(0,0,0,.15);white-space:nowrap}
.pill--on{background:var(--blue);color:var(--white)}

.photo{position:absolute;border-radius:6px;box-shadow:0 2px 5px rgba(0,0,0,.18)}
.section-title{position:absolute;font-family:"Rubik",Arial,sans-serif;font-weight:800;font-size:15px;color:var(--ink);letter-spacing:.2px;white-space:nowrap}

/* home */
.hero-home{left:0;top:46px;width:515px;height:290px;background:linear-gradient(160deg,#b08a4a 0%,#6e5230 45%,#2a2018 70%,#8a6a3e 100%)}
.thumb{position:absolute;top:268px;width:60px;height:44px;border-radius:4px;border:1px solid rgba(255,255,255,.6)}
.thumb-label{position:absolute;left:97px;top:286px;font-size:5.5px;color:var(--white)}
.dots{position:absolute;left:245px;top:326px;display:flex;gap:3px}
.dots i{width:3px;height:3px;border-radius:50%;background:rgba(255,255,255,.5)}
.dots i:first-child{background:var(--white)}
.story{left:0;top:626px;width:515px;height:292px;background:var(--story-bg)}
.story__band{left:0;top:0;width:172px;height:292px;background:var(--blue)}
.story__text{left:289px;top:86px;width:178px;font-size:5.6px;line-height:9.4px;color:#666;text-align:justify}
.video-band{left:0;top:918px;width:515px;height:301px;background:radial-gradient(circle at 50% 60%,#5b7ad6 0%,#24307a 35%,#0f1232 75%)}
.play{position:absolute;left:232px;top:999px;width:50px;height:50px;border-radius:50%;background:#c8b497;display:flex;align-items:center;justify-content:center}
.quote-card{position:absolute;left:65px;top:1131px;width:385px;height:128px;background:var(--white);border-radius:20px;display:flex;align-items:center;justify-content:center;text-align:center;font-size:11px;line-height:18px;color:var(--ink);padding:0 50px}

/* footer */
.site-footer{position:absolute;left:0;bottom:0;width:100%;background:var(--beige)}
.footer-body{position:absolute;left:0;width:100%;height:140px}
.footer-title{position:absolute;top:32px;font-family:"Rubik",Arial,sans-serif;font-weight:700;font-size:8px;color:var(--beige-text);letter-spacing:.3px}
.footer-links{position:absolute;left:64px;top:46px;list-style:none;font-size:6px;line-height:14.3px;color:var(--beige-text)}
.footer-contact{position:absolute;left:178px;top:44px;list-style:none;font-size:6px;line-height:14.3px;color:var(--beige-text)}
.footer-contact li{display:flex;align-items:center;gap:6px;white-space:nowrap}
.footer-contact li.indent{padding-left:13px}
.footer-contact svg{width:7px;height:7px;fill:var(--beige-text)}
.footer-logo{position:absolute;left:301px;top:26px}
.footer-logo .logo__name{font-size:20px;line-height:20px;color:var(--navy)}
.footer-logo .logo__tag{font-size:13px;line-height:16px;color:var(--beige-text);padding-left:25px;letter-spacing:1.3px}
.footer-rule{position:absolute;left:64px;top:123px;width:387px;height:1px;background:rgba(255,255,255,.55)}
.copyright{position:absolute;left:0;top:135px;width:100%;text-align:center;font-size:5px;color:var(--beige-text)}

/* magazine */
.hero-mag{left:0;top:50px;width:515px;height:208px;background:var(--blue-hero)}
.hero-title{position:absolute;left:47px;top:116px;font-family:"Rubik",Arial,sans-serif;font-weight:800;font-size:22px;color:var(--white);letter-spacing:.3px}
.hero-sub{position:absolute;left:47px;top:144px;font-size:8px;line-height:13px;color:var(--white)}
.card{position:absolute;width:134px;height:101px}
.caption{position:absolute;width:134px;text-align:center;font-size:5.8px;line-height:10px;color:#555}
.caption--on{color:var(--navy);font-weight:600}
.btn--more{left:219px;top:615px;width:77px;height:16px}

/* detail */
.hero-detail{left:0;top:46px;width:515px;height:220px;background:linear-gradient(180deg,#8a7a6e 0%,#b9a899 50%,#3f3a38 100%)}
.play-plain{position:absolute;left:243px;top:143px;width:30px;height:30px;border-radius:50%;background:var(--white);display:flex;align-items:center;justify-content:center}
.detail-title{position:absolute;left:0;top:298px;width:100%;text-align:center;font-family:"Rubik",Arial,sans-serif;font-weight:800;font-size:15px;color:var(--ink)}
.slide{position:absolute;top:333px;width:132px;height:94px;border-radius:4px}
.info{position:absolute;left:0;top:437px;width:100%;text-align:center;font-size:6px;line-height:11.8px;color:#666}
.info b{color:var(--ink);font-weight:600}
.detail-desc{position:absolute;left:120px;top:492px;width:275px;text-align:center;font-size:6px;line-height:11.8px;color:#666}
</style>
</head>
<body>
<div class="board">

  <!-- HOME -->
  <section class="screen screen--home">
    <header class="site-header">
      <div class="logo"><span class="logo__name">MARC DELEVAL</span><span class="logo__tag">Directeur Photo</span></div>
      <span class="nav" style="left:208px">Presentation</span>
      <span class="nav" style="left:264px">Magazine</span>
      <span class="nav" style="left:313px">Spectacle</span>
      <span class="nav" style="left:363px">Fiction/Event</span>
      <span class="btn btn--header">Talk Info</span>
    </header>
    <div class="abs hero-home" role="img" aria-label="Pianiste à un piano à queue dans un salon doré"></div>
    <div class="thumb" style="left:86px;background:linear-gradient(135deg,#1b4fb8,#3b7ad8)"></div>
    <span class="thumb-label">Now Playing...</span>
    <div class="thumb" style="left:157px;background:linear-gradient(135deg,#a09070,#4a3e2e)" role="img" aria-label="Vignette de tournage"></div>
    <div class="thumb" style="left:228px;background:linear-gradient(135deg,#6a5038,#2a2018)" role="img" aria-label="Vignette de concert"></div>
    <div class="thumb" style="left:298px;background:linear-gradient(135deg,#3a3a4a,#141420)" role="img" aria-label="Vignette de plateau"></div>
    <div class="thumb" style="left:368px;background:linear-gradient(135deg,#a03a6a,#3a1a5a)" role="img" aria-label="Vignette de soirée"></div>
    <div class="dots"><i></i><i></i><i></i><i></i></div>

    <h2 class="section-title" style="left:47px;top:366px">PHOTO GALLERY</h2>
    <span class="pill pill--on" style="left:274px;top:367px;width:26px">All</span>
    <span class="pill" style="left:309px;top:367px;width:47px">Magazine</span>
    <span class="pill" style="left:364px;top:367px;width:36px">Show</span>
    <span class="pill" style="left:407px;top:367px;width:60px">Fiction/Event</span>

    <div class="photo" style="left:47px;top:405px;width:99px;height:67px;background:linear-gradient(135deg,#4a3a30,#a05a3a)" role="img" aria-label="Plateau de débat"></div>
    <div class="photo" style="left:47px;top:485px;width:99px;height:68px;background:linear-gradient(135deg,#1a4ab0,#2a6ad0)" role="img" aria-label="Plateau d'émission en bleu"></div>
    <div class="photo" style="left:154px;top:405px;width:99px;height:148px;background:linear-gradient(180deg,#5a3a6a,#a03a4a 60%,#3a1a2a)" role="img" aria-label="Salle de gala illuminée"></div>
    <div class="photo" style="left:260px;top:405px;width:99px;height:67px;background:linear-gradient(135deg,#5a4a40,#2a2422)" role="img" aria-label="Interview en salon"></div>
    <div class="photo" style="left:260px;top:485px;width:99px;height:68px;background:linear-gradient(135deg,#7a8aa8,#3a4a6a)" role="img" aria-label="Plateau de talk-show"></div>
    <div class="photo" style="left:367px;top:405px;width:100px;height:148px;background:linear-gradient(180deg,#2a8ad0,#1a5ab0 60%,#0f2f70)" role="img" aria-label="Cérémonie de remise de trophées"></div>
    <span class="btn" style="left:226px;top:571px;width:64px;height:16px">Explore More</span>

    <div class="abs story">
      <div class="abs story__band"></div>
      <div class="photo" style="left:48px;top:59px;width:209px;height:174px;border-radius:10px;background:linear-gradient(135deg,#c07a3a,#4a2a1a 60%,#201410)" role="img" aria-label="Portrait du directeur photo en studio"></div>
      <h2 class="section-title" style="left:289px;top:62px">OUR STORY</h2>
      <p class="abs story__text">Lorem ipsum dolor sit amet, consectetur adipiscing elit, sed do eiusmod tempor incididunt ut labore et dolore magna aliqua. Ut enim ad minim veniam, quis nostrud exercitation ullamco laboris nisi ut aliquip ex ea commodo consequat. Duis aute irure dolor in reprehenderit in voluptate velit esse cillum dolore eu fugiat nulla pariatur.<br><br>Excepteur sint occaecat cupidatat non proident, sunt in culpa qui officia deserunt mollit anim id est laborum. Lorem ipsum dolor sit amet</p>
      <span class="btn" style="left:289px;top:210px;width:59px;height:16px">Learn More</span>
    </div>

    <div class="abs video-band" role="img" aria-label="Concert sur grande scène avec faisceaux lumineux"></div>
    <div class="play"><svg width="14" height="16" viewBox="0 0 14 16"><path d="M2 1 L13 8 L2 15 Z" fill="#fff"/></svg></div>

    <footer class="site-footer" style="height:196px">
      <div class="footer-body" style="top:39px">
        <span class="footer-title" style="left:64px">QUICK LINKS</span>
        <ul class="footer-links"><li>Home</li><li>Presentation</li><li>Magazine</li><li>Spectacle</li><li>Fiction</li></ul>
        <span class="footer-title" style="left:178px">CONTACT US</span>
        <ul class="footer-contact">
          <li><svg viewBox="0 0 10 10"><path d="M5 0a3.5 3.5 0 0 0-3.5 3.5C1.5 6 5 10 5 10s3.5-4 3.5-6.5A3.5 3.5 0 0 0 5 0zm0 5a1.4 1.4 0 1 1 0-2.8A1.4 1.4 0 0 1 5 5z"/></svg>Location: Marc Deleval</li>
          <li class="indent">United States</li>
          <li><svg viewBox="0 0 10 10"><path d="M2 0l2 2.5-1 1.5c.6 1.3 1.7 2.4 3 3l1.5-1L10 8l-1.5 2C4 9.5.5 6 0 1.5z"/></svg>Phone: 0612345678</li>
          <li><svg viewBox="0 0 10 10"><path d="M0 2h10v6H0zM0 2l5 3.5L10 2"/></svg>Email: contact@marcdeleval.fr</li>
        </ul>
        <div class="footer-logo"><span class="logo__name">MARC DELEVAL</span><span class="logo__tag">Directeur Photo</span></div>
        <div class="footer-rule"></div>
        <p class="copyright">Copyrights2026.Marc Deleval All Rights Reserved</p>
      </div>
    </footer>
    <div class="quote-card">Entertainment magazines, news programs, political debates, game shows, concert recordings, music videos, short fiction films, documentaries, commercials, and corporate films</div>
  </section>

  <!-- MAGAZINE -->
  <section class="screen screen--magazine">
    <header class="site-header">
      <div class="logo"><span class="logo__name">MARC DELEVAL</span><span class="logo__tag">Directeur Photo</span></div>
      <span class="nav" style="left:204px">Presentation</span>
      <span class="nav nav--active" style="left:260px">Magazine</span>
      <span class="nav" style="left:310px">Spectacle</span>
      <span class="nav" style="left:360px">Fiction/Event</span>
      <span class="btn btn--header">Talk Info</span>
    </header>
    <div class="abs hero-mag"></div>
    <svg class="abs" style="left:0;top:0" width="515" height="260" viewBox="0 0 515 260" role="img" aria-label="Photos de tournages de magazine en cadres inclinés">
      <defs>
        <linearGradient id="mg1" x1="0" y1="0" x2="1" y2="1"><stop offset="0" stop-color="#8a7a6a"/><stop offset="1" stop-color="#2a2422"/></linearGradient>
        <linearGradient id="mg2" x1="0" y1="0" x2="1" y2="1"><stop offset="0" stop-color="#a06a4a"/><stop offset="1" stop-color="#3a5a4a"/></linearGradient>
      </defs>
      <polygon points="228,50 398,50 420,118 312,176" fill="url(#mg1)" stroke="#fff" stroke-width="1.5"/>
      <polygon points="362,180 470,108 515,152 515,258 410,258" fill="url(#mg2)" stroke="#fff" stroke-width="1.5"/>
    </svg>
    <h1 class="hero-title">MAGAZINE</h1>
    <p class="hero-sub">Available for televison, commercial,<br>documentary &amp; branded projects.</p>

    <h2 class="section-title" style="left:47px;top:287px">OUR WORK</h2>
    <span class="pill pill--on" style="left:324px;top:287px;width:63px">Past Projects</span>
    <span class="pill" style="left:396px;top:287px;width:71px">Current Projects</span>

    <div class="photo card" style="left:47px;top:324px;background:linear-gradient(135deg,#7a4a3a,#c04a3a 60%,#3a2a2a)" role="img" aria-label="Plateau d'émission de vente"></div>
    <div class="photo card" style="left:190px;top:324px;background:linear-gradient(135deg,#9a8a7a,#4a3e36)" role="img" aria-label="Interview dans une salle à colonnes"></div>
    <div class="photo card" style="left:333px;top:324px;background:linear-gradient(135deg,#b04aa0,#d8d0d0 60%,#4a4040)" role="img" aria-label="Présentatrice sur plateau"></div>
    <p class="caption" style="left:47px;top:434px">Bonne Affaire<br>La quotidienne et les primes &nbsp;/ Télé Deux</p>
    <p class="caption" style="left:190px;top:434px">Un pays, un regard<br>mag hebdo / Chaîne Civique</p>
    <p class="caption" style="left:333px;top:434px">Le Grand zapping<br>lancements hebdo / Canal 12</p>
    <div class="photo card" style="left:47px;top:467px;background:linear-gradient(135deg,#d8c8a8,#a88a5a 60%,#e8e0d0)" role="img" aria-label="Plateau de cuisine"></div>
    <div class="photo card" style="left:190px;top:467px;background:linear-gradient(135deg,#6ab0e0,#2a6ab0 60%,#d0e0f0)" role="img" aria-label="Plateau météo"></div>
    <div class="photo card" style="left:333px;top:467px;background:linear-gradient(135deg,#8a4a2a,#4a2a1a)" role="img" aria-label="Bibliothèque ancienne"></div>
    <p class="caption caption--on" style="left:47px;top:577px">Îles en Vue, le mag<br>quotidienne &nbsp;/ Télé Trois</p>
    <p class="caption" style="left:190px;top:577px">Ciel à la carte<br>quot en direct / Télé Trois</p>
    <p class="caption" style="left:333px;top:577px">Pages &amp; Vous<br>mag littéraire mensuel &nbsp;/ Chaîne Civique</p>
    <span class="btn btn--more">View More Items</span>

    <footer class="site-footer" style="height:153px">
      <div class="footer-body" style="top:0">
        <span class="footer-title" style="left:64px">QUICK LINKS</span>
        <ul class="footer-links"><li>Home</li><li>Presentation</li><li>Magazine</li><li>Spectacle</li><li>Fiction</li></ul>
        <span class="footer-title" style="left:178px">CONTACT US</span>
        <ul class="footer-contact">
          <li><svg viewBox="0 0 10 10"><path d="M5 0a3.5 3.5 0 0 0-3.5 3.5C1.5 6 5 10 5 10s3.5-4 3.5-6.5A3.5 3.5 0 0 0 5 0zm0 5a1.4 1.4 0 1 1 0-2.8A1.4 1.4 0 0 1 5 5z"/></svg>Location: Marc Deleval</li>
          <li class="indent">United States</li>
          <li><svg viewBox="0 0 10 10"><path d="M2 0l2 2.5-1 1.5c.6 1.3 1.7 2.4 3 3l1.5-1L10 8l-1.5 2C4 9.5.5 6 0 1.5z"/></svg>Phone: 0612345678</li>
          <li><svg viewBox="0 0 10 10"><path d="M0 2h10v6H0zM0 2l5 3.5L10 2"/></svg>Email: contact@marcdeleval.fr</li>
        </ul>
        <div class="footer-logo"><span class="logo__name">MARC DELEVAL</span><span class="logo__tag">Directeur Photo</span></div>
        <div class="footer-rule"></div>
        <p class="copyright">Copyrights2026.Marc Deleval All Rights Reserved</p>
      </div>
    </footer>
  </section>

  <!-- DETAIL -->
  <section class="screen screen--detail">
    <header class="site-header">
      <div class="logo"><span class="logo__name">MARC DELEVAL</span><span class="logo__tag">Directeur Photo</span></div>
      <span class="nav" style="left:208px">Presentation</span>
      <span class="nav" style="left:264px">Magazine</span>
      <span class="nav" style="left:313px">Spectacle</span>
      <span class="nav" style="left:363px">Fiction/Event</span>
      <span class="btn btn--header">Talk Info</span>
    </header>
    <div class="abs hero-detail" role="img" aria-label="Interview dans une salle à statues et sol en damier"></div>
    <div class="play-plain"><svg width="10" height="12" viewBox="0 0 10 12"><path d="M1 0 L10 6 L1 12 Z" fill="#15368f"/></svg></div>
    <h2 class="detail-title">ÎLES EN VUE, LE MAG</h2>
    <svg class="abs" style="left:20px;top:374px" width="8" height="10" viewBox="0 0 8 10"><path d="M6 1 L2 5 L6 9" fill="none" stroke="#111" stroke-width="1.5"/></svg>
    <div class="slide" style="left:48px;background:linear-gradient(135deg,#e0d0b0,#8aa0b0)" role="img" aria-label="Présentateurs en cuisine"></div>
    <div class="slide" style="left:191px;background:linear-gradient(135deg,#d8c8a8,#a08a6a)" role="img" aria-label="Plateau de cuisine"></div>
    <div class="slide" style="left:334px;background:linear-gradient(135deg,#6a9ab8,#d0c0a8)" role="img" aria-label="Invitée en bord de mer"></div>
    <svg class="abs" style="left:485px;top:374px" width="8" height="10" viewBox="0 0 8 10"><path d="M2 1 L6 5 L2 9" fill="none" stroke="#111" stroke-width="1.5"/></svg>
    <p class="info"><b>EMISSION :</b> Îles en Vue, le mag<br><b>REALISE PAR :</b> Paul Verdier<br><b>DUREE :</b> 26 mn<br><b>DIFFUSEUR :</b> Télé Trois</p>
    <p class="detail-desc">Magazine de divertissement allant à la rencontre des insulaires qui partagent leurs passions ou leurs combats, en mettant en lumière la richesse gastronomique des territoires.<br><br>animé par Claire et Julien<br>----<br>Conception lumière</p>

    <footer class="site-footer" style="height:149px">
      <div class="footer-body" style="top:-5px">
        <span class="footer-title" style="left:64px">QUICK LINKS</span>
        <ul class="footer-links"><li>Home</li><li>Presentation</li><li>Magazine</li><li>Spectacle</li><li>Fiction</li></ul>
        <span class="footer-title" style="left:178px">CONTACT US</span>
        <ul class="footer-contact">
          <li><svg viewBox="0 0 10 10"><path d="M5 0a3.5 3.5 0 0 0-3.5 3.5C1.5 6 5 10 5 10s3.5-4 3.5-6.5A3.5 3.5 0 0 0 5 0zm0 5a1.4 1.4 0 1 1 0-2.8A1.4 1.4 0 0 1 5 5z"/></svg>Location: Marc Deleval</li>
          <li class="indent">United States</li>
          <li><svg viewBox="0 0 10 10"><path d="M2 0l2 2.5-1 1.5c.6 1.3 1.7 2.4 3 3l1.5-1L10 8l-1.5 2C4 9.5.5 6 0 1.5z"/></svg>Phone: 0612345678</li>
          <li><svg viewBox="0 0 10 10"><path d="M0 2h10v6H0zM0 2l5 3.5L10 2"/></svg>Email: contact@marcdeleval.fr</li>
        </ul>
        <div class="footer-logo"><span class="logo__name">MARC DELEVAL</span><span class="logo__tag">Directeur Photo</span></div>
        <div class="footer-rule"></div>
        <p class="copyright">Copyrights2026.Marc Deleval All Rights Reserved</p>
      </div>
    </footer>
  </section>

  <!-- MAGAZINE, PHOTO HERO -->
  <section class="screen screen--partner">
    <header class="site-header">
      <div class="logo"><span class="logo__name">MARC DELEVAL</span><span class="logo__tag">Directeur Photo</span></div>
      <span class="nav" style="left:204px">Presentation</span>
      <span class="nav nav--active" style="left:260px">Magazine</span>
      <span class="nav" style="left:310px">Spectacle</span>
      <span class="nav" style="left:360px">Fiction/Event</span>
      <span class="btn btn--header">Talk Info</span>
    </header>
    <div class="abs" style="left:0;top:50px;width:515px;height:208px;background:linear-gradient(100deg,#1a3a7a 0%,#2a5aa8 45%,#3aa06a 70%,#6a7ac0 100%)" role="img" aria-label="Plateau de cérémonie avec public et décor vert"></div>
    <h1 class="hero-title">MAGAZINE</h1>
    <p class="hero-sub">Available for televison, commercial,<br>documentary &amp; branded projects.</p>

    <h2 class="section-title" style="left:47px;top:287px">OUR WORK</h2>
    <span class="pill pill--on" style="left:324px;top:287px;width:63px">Past Projects</span>
    <span class="pill" style="left:396px;top:287px;width:71px">Current Projects</span>

    <div class="photo card" style="left:47px;top:324px;background:linear-gradient(135deg,#7a4a3a,#c04a3a 60%,#3a2a2a)" role="img" aria-label="Plateau d'émission de vente"></div>
    <div class="photo card" style="left:190px;top:324px;background:linear-gradient(135deg,#9a8a7a,#4a3e36)" role="img" aria-label="Interview dans une salle à colonnes"></div>
    <div class="photo card" style="left:333px;top:324px;background:linear-gradient(135deg,#b04aa0,#d8d0d0 60%,#4a4040)" role="img" aria-label="Présentatrice sur plateau"></div>
    <p class="caption" style="left:47px;top:434px">Bonne Affaire<br>La quotidienne et les primes &nbsp;/ Télé Deux</p>
    <p class="caption" style="left:190px;top:434px">Un pays, un regard<br>mag hebdo / Chaîne Civique</p>
    <p class="caption" style="left:333px;top:434px">Le Grand zapping<br>lancements hebdo / Canal 12</p>
    <div class="photo card" style="left:47px;top:467px;background:linear-gradient(135deg,#d8c8a8,#a88a5a 60%,#e8e0d0)" role="img" aria-label="Plateau de cuisine"></div>
    <div class="photo card" style="left:190px;top:467px;background:linear-gradient(135deg,#6ab0e0,#2a6ab0 60%,#d0e0f0)" role="img" aria-label="Plateau météo"></div>
    <div class="photo card" style="left:333px;top:467px;background:linear-gradient(135deg,#8a4a2a,#4a2a1a)" role="img" aria-label="Bibliothèque ancienne"></div>
    <p class="caption caption--on" style="left:47px;top:577px">Îles en Vue, le mag<br>quotidienne &nbsp;/ Télé Trois</p>
    <p class="caption" style="left:190px;top:577px">Ciel à la carte<br>quot en direct / Télé Trois</p>
    <p class="caption" style="left:333px;top:577px">Pages &amp; Vous<br>mag littéraire mensuel &nbsp;/ Chaîne Civique</p>
    <span class="btn btn--more">View More Items</span>

    <footer class="site-footer" style="height:153px">
      <div class="footer-body" style="top:0">
        <span class="footer-title" style="left:64px">QUICK LINKS</span>
        <ul class="footer-links"><li>Home</li><li>Presentation</li><li>Magazine</li><li>Spectacle</li><li>Fiction</li></ul>
        <span class="footer-title" style="left:178px">CONTACT US</span>
        <ul class="footer-contact">
          <li><svg viewBox="0 0 10 10"><path d="M5 0a3.5 3.5 0 0 0-3.5 3.5C1.5 6 5 10 5 10s3.5-4 3.5-6.5A3.5 3.5 0 0 0 5 0zm0 5a1.4 1.4 0 1 1 0-2.8A1.4 1.4 0 0 1 5 5z"/></svg>Location: Marc Deleval</li>
          <li class="indent">United States</li>
          <li><svg viewBox="0 0 10 10"><path d="M2 0l2 2.5-1 1.5c.6 1.3 1.7 2.4 3 3l1.5-1L10 8l-1.5 2C4 9.5.5 6 0 1.5z"/></svg>Phone: 0612345678</li>
          <li><svg viewBox="0 0 10 10"><path d="M0 2h10v6H0zM0 2l5 3.5L10 2"/></svg>Email: contact@marcdeleval.fr</li>
        </ul>
        <div class="footer-logo"><span class="logo__name">MARC DELEVAL</span><span class="logo__tag">Directeur Photo</span></div>
        <div class="footer-rule"></div>
        <p class="copyright">Copyrights2026.Marc Deleval All Rights Reserved</p>
      </div>
    </footer>
  </section>

</div>
</body>
</html>
```